design a construction company business card

Design business card around our logo. Card must have all the typical info: name, title, address, phone, email, business name, etc. Somewhere on the card I would like to see our motto "Built on integrity... Inspired by commitment." Consider adding a splash of bright orange to the card to complement the blues and silvers/grays in the logo. We are open to metallic inks, textures, etc. We would like to see options on both light and dark backgrounds. The font in the logo is Euro Technic Extended Regular.

```html
<!DOCTYPE html>
<html lang="en">
<head>
<meta charset="utf-8">
<title>Harlow Building Co. – Business Card</title>
<link rel="stylesheet" href="https://fonts.googleapis.com/css2?family=Roboto:ital,wght@0,400;0,500;0,700;1,700&display=swap">
<style>
  :root {
    --stage: #d2d3d5;
    --paper: #ffffff;
    --brand-blue: #2a54a6;
    --deep-blue: #2b358e;
    --top-blue: #2358a6;
    --ink-gray: #6b6b6b;
    --rule-gray: #8a8a8a;
    --orange-dark: #f07033;
    --orange-light: #f7a83c;
    --icon-navy: #1f3a6e;
  }
  * { margin: 0; padding: 0; box-sizing: border-box; }
  html, body { width: 1200px; height: 1200px; overflow: hidden; }
  body {
    background: var(--stage);
    font-family: "Roboto", Arial, sans-serif;
    position: relative;
  }
  .card {
    position: absolute;
    left: 310px;
    width: 570px;
    height: 354px;
    overflow: hidden;
  }
  .card--front { top: 226px; background: var(--paper); }
  .card--back {
    top: 620px;
    background: linear-gradient(180deg, var(--top-blue) 0%, var(--deep-blue) 100%);
  }

  /* front */
  .brand-name {
    position: absolute;
    left: 42px;
    top: 110px;
    width: 212px;
    text-align: center;
    color: var(--brand-blue);
    font-weight: 700;
    line-height: 1.05;
  }
  .brand-name .mark {
    display: block;
    width: 22px; height: 22px;
    margin: 0 auto 10px;
    background: var(--brand-blue);
  }
  .brand-name .word { display: block; font-size: 40px; letter-spacing: 3px; }
  .brand-name .sub { display: block; font-size: 15px; letter-spacing: 2px; margin-top: 4px; }

  .divider {
    position: absolute;
    left: 285px; top: 46px;
    width: 2px; height: 234px;
    background: var(--rule-gray);
  }
  .person {
    position: absolute;
    left: 304px; top: 66px;
    color: var(--ink-gray);
  }
  .person__name { font-size: 29px; font-weight: 400; letter-spacing: 0.5px; line-height: 1; }
  .person__title { font-size: 14.5px; margin-top: 3px; }

  .contact-list { list-style: none; position: absolute; left: 302px; top: 0; }
  .contact-item {
    position: absolute;
    left: 0;
    display: flex;
    align-items: flex-start;
    gap: 9px;
    color: var(--ink-gray);
    font-size: 13.5px;
    line-height: 1.3;
    white-space: nowrap;
  }
  .contact-item svg { flex: none; width: 30px; height: 30px; }
  .contact-item span { padding-top: 5px; }
  .contact-item--address { top: 138px; }
  .contact-item--phone { top: 186px; }
  .contact-item--email { top: 230px; }

  .footer-band {
    position: absolute;
    left: 0; bottom: 0;
    width: 100%; height: 35px;
    border-top: 5px solid var(--brand-blue);
    background: linear-gradient(90deg, var(--orange-dark) 0%, var(--orange-light) 50%, var(--orange-dark) 100%);
    text-align: center;
    font-size: 14px;
    line-height: 30px;
    color: #1c1c1c;
  }

  /* back */
  .brand-name--reverse {
    left: 0; top: 86px;
    width: 100%;
    color: #ffffff;
  }
  .brand-name--reverse .mark { background: #ffffff; width: 26px; height: 26px; }
  .brand-name--reverse .word { font-size: 54px; letter-spacing: 4px; }
  .brand-name--reverse .sub { font-size: 19px; letter-spacing: 3px; }

  .motto {
    position: absolute;
    left: 0; top: 262px;
    width: 100%;
    text-align: center;
    color: #ffffff;
    font-size: 20px;
    font-weight: 700;
    font-style: italic;
  }
</style>
</head>
<body>

<section class="card card--front" aria-label="Business card front">
  <div class="brand-name">
    <span class="mark"></span>
    <span class="word">HARLOW</span>
    <span class="sub">BUILDING CO.</span>
  </div>

  <div class="divider"></div>

  <div class="person">
    <p class="person__name">DANIEL REYES</p>
    <p class="person__title">General Contractor</p>
  </div>

  <ul class="contact-list">
    <li class="contact-item contact-item--address">
      <svg viewBox="0 0 30 30" aria-hidden="true">
        <circle cx="15" cy="15" r="13.5" fill="#fff" stroke="#9a9a9a" stroke-width="2"/>
        <path d="M15 7.5a5 5 0 0 0-5 5c0 3.8 5 9.5 5 9.5s5-5.7 5-9.5a5 5 0 0 0-5-5z" fill="var(--icon-navy)"/>
        <circle cx="15" cy="12.5" r="2" fill="#fff"/>
      </svg>
      <span>4218 Cedarbend Ave. Houston<br>TX 77041</span>
    </li>
    <li class="contact-item contact-item--phone">
      <svg viewBox="0 0 30 30" aria-hidden="true">
        <circle cx="15" cy="15" r="13.5" fill="#fff" stroke="#9a9a9a" stroke-width="2"/>
        <path d="M10.5 8.5l2.2-.6 1.6 3.3-1.5 1.2c.8 1.8 2 3 3.8 3.9l1.2-1.5 3.3 1.6-.6 2.2c-.3.8-1 1.2-1.9 1.1-4.4-.6-8-4.2-8.6-8.6-.1-.9.3-1.6 1.1-1.9z" fill="var(--icon-navy)"/>
        <path d="M16.5 9.5a4.5 4.5 0 0 1 4 4M16.5 7a7 7 0 0 1 6.5 6.5" fill="none" stroke="var(--icon-navy)" stroke-width="1.3" stroke-linecap="round"/>
      </svg>
      <span>713-555-0148</span>
    </li>
    <li class="contact-item contact-item--email">
      <svg viewBox="0 0 30 30" aria-hidden="true">
        <circle cx="15" cy="15" r="13.5" fill="#fff" stroke="#9a9a9a" stroke-width="2"/>
        <rect x="8.5" y="10.5" width="13" height="9" fill="var(--icon-navy)"/>
        <path d="M8.8 10.8l6.2 5 6.2-5" fill="none" stroke="#fff" stroke-width="1.1"/>
      </svg>
      <span>dreyes@harlowbuilding.com</span>
    </li>
  </ul>

  <div class="footer-band">www.harlowbuildingco.com</div>
</section>

<section class="card card--back" aria-label="Business card back">
  <div class="brand-name brand-name--reverse">
    <span class="mark"></span>
    <span class="word">HARLOW</span>
    <span class="sub">BUILDING CO.</span>
  </div>
  <p class="motto">“Grounded in quality...Driven by dedication”</p>
</section>

</body>
</html>
```